Business Card Design

I already have a company logo for my company. I have a logo for the manufacturer we represent. I want a professional business card design.

```html
<!DOCTYPE html>
<html lang="en">
<head>
<meta charset="utf-8">
<title>Beacon Alert Co. — Business Card</title>
<link href="https://fonts.googleapis.com/css2?family=Lato:wght@400;700;900&display=swap" rel="stylesheet">
<style>
  :root {
    --stage: #2a2b2d;
    --card-white: #ffffff;
    --card-black: #1c1c1e;
    --brand-red: #e01f26;
    --brand-gold: #e0a526;
    --ink: #1a1a1a;
    --muted: #6b6b6b;
    --rule: #9a9a9a;
  }
  * { box-sizing: border-box; margin: 0; padding: 0; }
  html, body { width: 1200px; height: 952px; overflow: hidden; }
  body {
    background: var(--stage);
    font-family: "Lato", sans-serif;
    position: relative;
  }
  .card {
    position: absolute;
    width: 560px;
    height: 320px;
    box-shadow: 0 18px 40px rgba(0,0,0,.45);
  }

  /* Front side */
  .card--front {
    left: 560px;
    top: 90px;
    background: var(--card-white);
    overflow: hidden;
  }
  .card__edge {
    position: absolute;
    left: 0; top: 0;
    width: 14px; height: 100%;
    background: var(--brand-red);
  }
  .card__tab {
    position: absolute;
    left: 0; top: 34px;
    width: 70px; height: 44px;
    background: var(--brand-red);
    border-radius: 0 22px 22px 0;
    display: flex; align-items: center; justify-content: flex-end;
    padding-right: 14px;
  }
  .card__tab svg { width: 20px; height: 20px; }
  .identity {
    position: absolute;
    left: 86px; top: 34px;
  }
  .identity__name {
    font-size: 28px;
    font-weight: 400;
    letter-spacing: 1px;
    color: var(--ink);
    line-height: 1;
  }
  .identity__name .surname { color: var(--brand-gold); font-weight: 700; }
  .identity__role {
    margin-top: 6px;
    font-size: 14px;
    color: var(--muted);
  }
  .contacts {
    position: absolute;
    left: 40px; top: 118px;
    list-style: none;
  }
  .contact {
    display: flex;
    align-items: center;
    margin-bottom: 14px;
  }
  .contact__icon { width: 22px; height: 22px; }
  .contact__slash {
    width: 1px; height: 26px;
    background: var(--rule);
    transform: rotate(20deg);
    margin: 0 14px 0 10px;
  }
  .contact__text {
    font-size: 13px;
    line-height: 1.35;
    color: var(--muted);
  }
  .brand {
    position: absolute;
    display: flex;
    align-items: center;
    gap: 10px;
  }
  .brand__square {
    width: 18px; height: 18px;
    background: var(--brand-red);
  }
  .brand__name {
    font-weight: 900;
    color: var(--brand-red);
    letter-spacing: 1px;
    text-transform: uppercase;
  }
  .card--front .brand { right: 36px; bottom: 40px; }
  .card--front .brand__name { font-size: 24px; }

  /* Back side */
  .card--back {
    left: 80px;
    top: 520px;
    background: var(--card-black);
    display: flex;
    align-items: center;
    justify-content: center;
  }
  .card--back .brand { position: static; }
  .card--back .brand__square { width: 24px; height: 24px; }
  .card--back .brand__name { font-size: 34px; }
</style>
</head>
<body>

  <section class="card card--front" aria-label="Business card front">
    <div class="card__edge"></div>
    <div class="card__tab">
      <svg viewBox="0 0 20 20" aria-hidden="true">
        <circle cx="10" cy="6" r="4" fill="#fff"/>
        <path d="M2 19c0-5 3.5-8 8-8s8 3 8 8z" fill="#fff"/>
      </svg>
    </div>
    <div class="identity">
      <h1 class="identity__name">JORDAN <span class="surname">PIERCE</span></h1>
      <p class="identity__role">Marketing Manager</p>
    </div>

    <ul class="contacts">
      <li class="contact">
        <svg class="contact__icon" viewBox="0 0 24 24" aria-hidden="true">
          <path d="M7 3l3 4-2 2c1 2.5 3.5 5 6 6l2-2 4 3-2 4C10 19 5 14 3 6z" fill="#1a1a1a"/>
        </svg>
        <span class="contact__slash"></span>
        <p class="contact__text">+1 555 0148 2290<br>+1 555 0148 2291</p>
      </li>
      <li class="contact">
        <svg class="contact__icon" viewBox="0 0 24 24" aria-hidden="true">
          <path d="M3 11L21 3l-8 18-2-8z" fill="#1a1a1a"/>
        </svg>
        <span class="contact__slash"></span>
        <p class="contact__text">www.beaconalert.example<br>hello@beaconalert.example</p>
      </li>
      <li class="contact">
        <svg class="contact__icon" viewBox="0 0 24 24" aria-hidden="true">
          <path d="M12 3L2 12h3v9h5v-6h4v6h5v-9h3z" fill="#1a1a1a"/>
        </svg>
        <span class="contact__slash"></span>
        <p class="contact__text">48 Harbor Lane, Millbrook,<br>Ohio, zip 44021.</p>
      </li>
    </ul>

    <div class="brand">
      <span class="brand__square"></span>
      <span class="brand__name">Beacon Alert Co.</span>
    </div>
  </section>

  <section class="card card--back" aria-label="Business card back">
    <div class="brand">
      <span class="brand__square"></span>
      <span class="brand__name">Beacon Alert Co.</span>
    </div>
  </section>

</body>
</html>
```